UL Aesthetic improvement on full website

brightneighbourhq.com
We need someone to improve the current website brightneighbourhq.com
Some designed to fail to follow isntruction and deliver. please find attached summary latest design requirement, please follow and read each of the requirements carefully and submit max two versions only. The winner would have to deliver within 5 days

Sample reference : velmorq.com/html/brightneighbour/#
(previous winner cant deliver)
*All of our wording and graphic content are updated, designer wouldn't involve in recreating any content.
Designer may use template or own material. delivery in html and implement on our WordPress server

please submit about us the project submission.
upon the winning, you have to maintain sub content / pages and submit the full site with your improved version of full websites including inner pages

Low design quality

Target Market(s)

general audience

Industry/Entity Type

social service

Number of Pages Required

5+ page

Requirements
Must have
• feeling and look similar to pobrix dot com
Nice to have
• extend the same style to other pages

```html
<!DOCTYPE html>
<html lang="en">
<head>
<meta charset="utf-8">
<title>Bright Neighbour — New Way of Giving</title>
<link href="https://fonts.googleapis.com/css2?family=Heebo:wght@300;400;500;700&family=Roboto:wght@400;500;700&display=swap" rel="stylesheet">
<style>
:root{
  --red:#f4575f;
  --ink:#1d1d1f;
  --text:#3a3a3c;
  --lavender:#f2f3fc;
  --pink:#fde4e8;
  --card-shadow:0 6px 28px rgba(40,50,120,.08);
  --badge:#e4e4ea;
}
*{box-sizing:border-box;margin:0;padding:0}
html,body{width:1200px;height:2895px;overflow:hidden}
body{position:relative;font-family:"Heebo",sans-serif;color:var(--text);
  background:linear-gradient(180deg,#fff 0,#fff 560px,var(--lavender) 900px,var(--lavender) 1200px,#fff 1300px,#fff 100%)}
.abs{position:absolute}
/* nav */
.brand{left:112px;top:42px;display:flex;align-items:center;gap:10px;color:var(--red);font:700 20px "Heebo",sans-serif;letter-spacing:1px}
.brand .dot{width:34px;height:34px;border-radius:50%;background:var(--red)}
.nav{left:459px;top:38px;display:flex;gap:30px;font:400 16.5px "Heebo",sans-serif;color:var(--ink)}
.login{left:946px;top:27px;width:141px;height:47px;border:2px solid var(--red);border-radius:24px;color:var(--red);
  font:500 16px "Heebo",sans-serif;display:flex;align-items:center;justify-content:center;gap:8px}
/* hero */
.eyebrow{left:112px;top:273px;font:400 24px "Heebo",sans-serif;color:var(--ink)}
.hero-title{left:112px;top:306px;font:700 45px "Roboto",sans-serif;color:var(--red)}
.store{top:385px;height:55px;background:#111;border:1.5px solid #555;border-radius:7px;color:#fff;display:flex;flex-direction:column;justify-content:center;padding-left:22px}
.store small{font-size:12px;line-height:1}
.store b{font:500 24px "Heebo",sans-serif;line-height:1.05}
.hero-art{left:568px;top:124px;width:552px;height:539px}
/* waves */
.wave{left:0;width:1200px}
/* intro */
.media{left:112px;width:462px;box-shadow:var(--card-shadow)}
.heading{font:700 34px "Roboto",sans-serif;color:var(--red)}
.copy{width:440px;font:300 14.5px/27.4px "Heebo",sans-serif;color:var(--ink)}
.copy p+p{margin-top:6px}
.copy strong{font-weight:500}
/* cards */
.card{top:1395px;width:306px;height:239px;background:#fff;border-radius:14px;box-shadow:var(--card-shadow);text-align:center;padding-top:30px}
.card .icon{width:64px;height:62px;margin:0 auto;border-radius:50%}
.card h3{font:500 26px "Roboto",sans-serif;color:var(--ink);margin-top:14px}
.card p{font:300 15px/24px "Heebo",sans-serif;color:var(--ink);margin:10px 22px 0}
/* partners */
.partners-title{left:0;width:1200px;top:2208px;text-align:center;font:700 23px "Roboto",sans-serif;color:var(--red)}
.badge{background:var(--badge);border-radius:6px}
/* footer */
.tagline{left:112px;top:2622px;font:500 18px/24px "Heebo",sans-serif;color:var(--ink)}
.social{top:2718px;width:52px;height:52px;border:1.5px solid var(--ink);border-radius:50%;display:flex;align-items:center;justify-content:center;font:500 12px "Heebo",sans-serif;color:var(--ink)}
.links{top:2626px;display:flex;flex-direction:column;gap:13px;font:500 15.5px "Heebo",sans-serif;color:var(--ink)}
.news-title{left:806px;top:2625px;font:500 18px "Heebo",sans-serif;color:var(--ink)}
.news-copy{left:806px;top:2656px;width:290px;font:400 14px/20px "Heebo",sans-serif;color:var(--ink)}
.email{left:809px;top:2727px;width:279px;height:45px;border:1.5px solid var(--ink);border-radius:23px;display:flex;align-items:center;justify-content:space-between;padding:0 18px;font:400 13px "Heebo",sans-serif;color:var(--ink)}
.copyright{left:0;width:1200px;top:2829px;text-align:center;font:400 15px "Heebo",sans-serif;color:var(--ink)}
</style>
</head>
<body>

<header>
  <div class="abs brand"><span class="dot"></span>BRIGHT NEIGHBOUR</div>
  <nav class="abs nav"><span>Home</span><span>About Us</span><span>Our Story</span><span>Social Impact</span><span>Join Us ⌄</span></nav>
  <div class="abs login">
    <svg width="13" height="14" viewBox="0 0 13 14"><circle cx="6.5" cy="4" r="3.5" fill="#f4575f"/><path d="M0 14c0-4 3-6 6.5-6S13 10 13 14z" fill="#f4575f"/></svg>LOGIN
  </div>
</header>

<section class="hero">
  <div class="abs eyebrow">NEW WAY OF GIVING</div>
  <h1 class="abs hero-title">SOCIAL INCLUSION</h1>
  <div class="abs store" style="left:112px;width:186px"><small>Download on the</small><b>AppHarbor</b></div>
  <div class="abs store" style="left:309px;width:181px"><small>GET IT ON</small><b>PlayDock</b></div>
  <svg class="abs hero-art" role="img" aria-label="Three phones showing the giving app on a red blob background" viewBox="0 0 552 539">
    <path d="M120 40C200 0 310 10 380 70 460 30 560 60 540 190 530 260 500 300 420 340 400 420 330 470 250 470 170 470 120 420 90 360 10 330-10 250 20 180 40 120 70 70 120 40Z" fill="#f4575f"/>
    <rect x="106" y="110" width="150" height="320" rx="20" fill="#f8f0f1"/>
    <rect x="330" y="110" width="150" height="320" rx="20" fill="#f3eef8"/>
    <rect x="216" y="60" width="160" height="330" rx="22" fill="#fff6e6"/>
  </svg>
</section>

<svg class="abs wave" style="top:1160px" height="140" viewBox="0 0 1200 140" preserveAspectRatio="none"><path d="M0 80C200 0 380 0 560 50 760 110 980 120 1200 50V140H0Z" fill="#fff"/></svg>

<section class="intro">
  <svg class="abs media" style="top:768px;height:288px" role="img" aria-label="Video still of a blue line drawing of a city skyline" viewBox="0 0 462 288">
    <rect width="462" height="288" fill="#fff"/>
    <path d="M0 120C120 60 240 40 462 90V288H0Z" fill="#d6e3fb"/>
    <rect y="250" width="462" height="38" fill="#d9d9dd"/>
    <circle cx="231" cy="144" r="30" fill="#fff" stroke="#3a3f9e" stroke-width="2"/>
    <path d="M222 130 246 144 222 158Z" fill="#3a3f9e"/>
  </svg>
  <h2 class="abs heading" style="left:643px;top:772px">HELLO, BRIGHT NEIGHBOURS!</h2>
  <div class="abs copy" style="left:643px;top:822px">
    <p>Just like you, we resonate with a variety of social causes. At the core of everything, we believe that many societal challenges could be minimized merely by being more kind to one another and showing more trust in each other, especially during these difficult times.</p>
    <p>Therefore, we digitalised the traditional concept of <strong>“Paying-it-forward”</strong> to cultivate the new normal with timely help to include everyone. We strengthens the invisible community before it’s too late.</p>
  </div>
</section>

<section class="values">
  <article class="abs card" style="left:112px">
    <div class="icon" role="img" aria-label="Icon of a thinking person" style="background:#fbd9c4"></div>
    <h3>Our Philosophy</h3>
    <p>We believe in authentic social responsibility is driven from individuals and businesses.</p>
  </article>
  <article class="abs card" style="left:446px">
    <div class="icon" role="img" aria-label="Icon of a dart in a target" style="background:#f9c6ca"></div>
    <h3>Our Mission</h3>
    <p>We connect individuals and businesses to support where it needs most in an easy, transparent, and holistic way</p>
  </article>
  <article class="abs card" style="left:780px">
    <div class="icon" role="img" aria-label="Icon of a clock with a forward arrow" style="background:#cfe2f6"></div>
    <h3>Our Future</h3>
    <p>Together, social impact as part of DNA at the heart of every consumption and business.</p>
  </article>
</section>

<section class="story">
  <div class="abs media" style="top:1746px;height:385px;background:linear-gradient(180deg,#cfe9ee 0%,#cfe9ee 45%,#f6c7ce 60%,#f3a9b4 100%)" role="img" aria-label="Illustration of people climbing a hill toward a city with a ferris wheel, labelled bridging for timely help"></div>
  <h2 class="abs heading" style="left:643px;top:1751px">THE BRAND STORY</h2>
  <div class="abs copy" style="left:643px;top:1799px">
    <p>Back in the 1980s, my family received generous donations and small handwritten notes containing good wishes through a newspaper fund raising for my mum’s medical expenses. I vividly remember some old and tattered notes from strangers. We ended up with double the amount that was needed, and my parents used the remaining sum to support other patients.</p>
    <p style="margin-top:15px">This was a valuable experience about paying it forward, about showing random kindness and integrity – about doing the right thing even when no one is watching...</p>
  </div>
</section>

<section class="partners">
  <h2 class="abs partners-title">OUR PARTNERS</h2>
  <div class="abs badge" style="left:114px;top:2284px;width:142px;height:36px"></div>
  <div class="abs badge" style="left:299px;top:2284px;width:160px;height:34px"></div>
  <div class="abs badge" style="left:510px;top:2286px;width:80px;height:32px"></div>
  <div class="abs badge" style="left:662px;top:2288px;width:60px;height:28px"></div>
  <div class="abs badge" style="left:834px;top:2282px;width:78px;height:38px"></div>
  <div class="abs badge" style="left:1004px;top:2286px;width:88px;height:32px"></div>
  <div class="abs badge" style="left:146px;top:2352px;width:78px;height:28px"></div>
  <div class="abs badge" style="left:342px;top:2348px;width:74px;height:36px"></div>
  <div class="abs badge" style="left:502px;top:2348px;width:96px;height:38px"></div>
  <div class="abs badge" style="left:641px;top:2352px;width:100px;height:30px"></div>
  <div class="abs badge" style="left:784px;top:2352px;width:180px;height:30px"></div>
</section>

<svg class="abs wave" style="top:2480px" height="415" viewBox="0 0 1200 415" preserveAspectRatio="none"><path d="M0 100C160 20 300 0 470 40 700 100 900 110 1200 50V415H0Z" fill="#fde4e8"/></svg>

<footer>
  <p class="abs tagline">A Singapore Social Enterprise.<br>In a world where you can be<br>anything, be kind.</p>
  <div class="abs social" style="left:112px">Hive</div>
  <div class="abs social" style="left:171px">Chirp</div>
  <div class="abs social" style="left:230px">Linkr</div>
  <div class="abs social" style="left:289px">Snapr</div>
  <div class="abs links" style="left:484px"><span>Home</span><span>About Us</span><span>Our Story</span><span>Social Impact</span><span>Bright Neighbour</span></div>
  <div class="abs links" style="left:614px"><span>Bright Business</span><span>Merchant</span><span>The Bright Gift</span><span>FAQs</span><span>Contact Us</span></div>
  <h3 class="abs news-title">SUBSCRIBE TO OUR NEWSLETTER</h3>
  <p class="abs news-copy">Let’s stay in touch! We would like to keep you inspired with our Kindness stories and community events.</p>
  <div class="abs email"><span>Email Address</span>
    <svg width="15" height="15" viewBox="0 0 15 15"><path d="M15 0 0 6l5 2 1 7 3-5 4 2z" fill="#1d1d1f"/></svg>
  </div>
  <p class="abs copyright">COPYRIGHT © 2021 BRIGHT NEIGHBOUR SINGAPORE</p>
</footer>

</body>
</html>
```